Landing Page / Waitlist

I would like a landing page for people to sign up for a waiting list. The text on the page should include (but is not limited to):
1) Main point: The accounting system you'll love
2) Secondary points:
a. Ruthlessly efficient
b. Quietly intelligent
c. Driven by AI
I've attached a file of our logo

The design should be simple, clean, and innovative - this is an ai company

```html
<!DOCTYPE html>
<html lang="en">
<head>
<meta charset="utf-8">
<title>Evenledger — Join the Waitlist</title>
<link href="https://fonts.googleapis.com/css2?family=Outfit:wght@300;400;500;600;700&display=swap" rel="stylesheet">
<style>
  :root{
    --blue:#0f8df5;
    --blue-bright:#00b2ff;
    --blue-deep:#0a84ff;
    --ink-dark:#15171c;
    --hero-warm:#3a2a1c;
    --white:#ffffff;
    --text:#4a4d55;
    --muted:#5e6169;
  }
  *{margin:0;padding:0;box-sizing:border-box}
  html,body{width:1200px;height:1060px;overflow:hidden;background:var(--white)}
  body{font-family:"Outfit",sans-serif;position:relative}
  .page{position:relative;width:1200px;height:1060px;overflow:hidden}

  .hero-backdrop{
    position:absolute;left:0;top:0;width:1200px;height:760px;
    background:
      radial-gradient(ellipse at 18% 30%, rgba(120,80,45,.55), transparent 60%),
      radial-gradient(ellipse at 45% 60%, rgba(90,70,55,.45), transparent 55%),
      linear-gradient(135deg,#2a1f17 0%,#1c1a1a 45%,#111419 100%);
    clip-path:polygon(0 0,1200px 0,1200px 641px,600px 700px,0 641px);
  }
  .hero-emblem{
    position:absolute;left:640px;top:30px;width:520px;height:520px;
    background:radial-gradient(circle at 55% 50%, rgba(20,150,255,.55) 0%, rgba(10,110,230,.25) 38%, transparent 68%);
  }
  .accent{position:absolute;left:0;top:0}

  .brand{
    position:absolute;left:110px;top:166px;
    font-size:52px;font-weight:600;color:var(--white);letter-spacing:-1px;line-height:1;
  }
  .headline{
    position:absolute;left:110px;top:280px;
    font-size:57px;line-height:59px;color:var(--blue);font-weight:600;letter-spacing:-.5px;
  }
  .headline .light{font-weight:400}
  .lede{
    position:absolute;left:110px;top:410px;width:470px;
    font-size:19px;line-height:29px;color:var(--white);font-weight:400;
  }
  .cta{
    position:absolute;left:110px;top:492px;width:166px;height:43px;
    background:var(--blue);color:var(--white);border-radius:4px;
    font-size:16px;font-weight:600;display:flex;align-items:center;justify-content:center;
    text-decoration:none;
  }

  .feature{
    position:absolute;text-align:center;background:var(--white);
    border:1px solid #4aa8f5;
  }
  .feature h2{font-size:16px;font-weight:500;color:var(--blue);margin:10px 0 9px}
  .feature p{font-size:13.5px;line-height:23px;color:var(--muted);font-weight:300}
  .feature .hex{display:block;margin:0 auto}
  .feature--left{left:206px;top:606px;width:242px;height:261px;padding:24px 18px 0}
  .feature--right{left:753px;top:606px;width:243px;height:261px;padding:24px 18px 0}
  .feature--center{
    left:448px;top:573px;width:306px;height:326px;padding:57px 18px 0;
    background:linear-gradient(135deg,var(--blue-bright),var(--blue-deep));
    border:none;box-shadow:0 10px 40px rgba(10,130,255,.15);
  }
  .feature--center h2{color:var(--white)}
  .feature--center p{color:var(--white);font-weight:400}

  .footer-links{
    position:absolute;left:0;top:946px;width:1200px;text-align:center;
    font-size:15.5px;color:var(--text);font-weight:300;
  }
  .footer-links a{color:var(--text);text-decoration:none}
  .footer-links .sep{margin:0 30px}
  .copyright{
    position:absolute;left:0;top:983px;width:1200px;text-align:center;
    font-size:12.5px;color:var(--text);font-weight:300;
  }
</style>
</head>
<body>
<main class="page">
  <div class="hero-backdrop" role="img" aria-label="Darkened photo of a person writing figures in a notebook at a desk"></div>
  <div class="hero-emblem" role="img" aria-label="Large glowing blue emblem surrounded by faint business icons"></div>

  <svg class="accent" width="1200" height="1060" viewBox="0 0 1200 1060" aria-hidden="true">
    <polygon points="36,654 206,688 206,710" fill="var(--blue-bright)"/>
    <polygon points="1164,654 996,688 996,710" fill="var(--blue-bright)"/>
    <polygon points="317,1060 600,1034 883,1060" fill="var(--blue-bright)"/>
  </svg>

  <div class="brand">Evenledger</div>

  <h1 class="headline">The Accounting<br>System <span class="light">You’ll Love</span></h1>
  <p class="lede">AI-powered. Effortless. Designed for the way modern businesses work.</p>
  <a class="cta" href="#">Join the Waitlist</a>

  <section class="feature feature--left">
    <svg class="hex" width="60" height="62" viewBox="0 0 60 62" aria-hidden="true">
      <polygon points="30,2 57,17 57,45 30,60 3,45 3,17" fill="var(--blue)"/>
      <path d="M19 33a11 11 0 0 1 19-9" stroke="#fff" stroke-width="3" fill="none"/>
      <path d="M41 29a11 11 0 0 1-19 9" stroke="#fff" stroke-width="3" fill="none"/>
      <polygon points="40,19 41,27 33,26" fill="#fff"/>
      <polygon points="20,43 19,35 27,36" fill="#fff"/>
      <path d="M24 36l12-11" stroke="#fff" stroke-width="3"/>
    </svg>
    <h2>Ruthlessly Efficient</h2>
    <p>Automate the tasks you hate — reconciliation, categorisation, reporting, and compliance — all handled in seconds with AI precision.</p>
  </section>

  <section class="feature feature--center">
    <svg class="hex" width="60" height="62" viewBox="0 0 60 62" aria-hidden="true">
      <polygon points="30,2 57,17 57,45 30,60 3,45 3,17" fill="#fff"/>
      <circle cx="25" cy="31" r="10" fill="none" stroke="var(--blue)" stroke-width="3"/>
      <path d="M35 24h8M35 31h10M35 38h8" stroke="var(--blue)" stroke-width="2.5"/>
      <circle cx="45" cy="24" r="2" fill="var(--blue)"/>
      <circle cx="47" cy="31" r="2" fill="var(--blue)"/>
      <circle cx="45" cy="38" r="2" fill="var(--blue)"/>
    </svg>
    <h2>Quietly Intelligent</h2>
    <p>Evenledger works in the background, understanding your workflows, predicting what you need, and reducing your workload without ever getting in the way.</p>
  </section>

  <section class="feature feature--right">
    <svg class="hex" width="60" height="62" viewBox="0 0 60 62" aria-hidden="true">
      <polygon points="30,2 57,17 57,45 30,60 3,45 3,17" fill="var(--blue)"/>
      <rect x="20" y="22" width="20" height="18" rx="5" fill="none" stroke="#fff" stroke-width="3"/>
      <circle cx="26" cy="30" r="2" fill="#fff"/>
      <circle cx="34" cy="30" r="2" fill="#fff"/>
      <path d="M30 22v-5M17 29v4M43 29v4" stroke="#fff" stroke-width="3"/>
    </svg>
    <h2>Driven by AI</h2>
    <p>A system that learns your business, adapts as you grow, and gives you clarity before you even ask for it.</p>
  </section>

  <nav class="footer-links">
    <a href="#">About Evenledger</a><span class="sep">|</span><a href="#">Privacy Policy</a><span class="sep">|</span><a href="#">Terms and Conditions</a>
  </nav>
  <p class="copyright">(C) Copyright 2025 | All Rights Reserved</p>
</main>
</body>
</html>
```